Elegant & Eye-Catching Brochure- Photo Booth Rentals

We rent photo booths for weddings, sweet 16's, parties, mitzvah's, school and corporate events and we would like to create a vibrant and fun, yet professional brochure to be attractive to the entire spectrum of potential clients. The brochure will be the standard tri-fold style (8.5"x11") and will have 3 inside panels and 3 outside panels.

Ideally this brochure would be elegant, classy, and professional, but still vibrant and fun. We have many colorful images that convey the quality of our photos and options, we want to highlight that aspect, but also would like to maintain that we are a great selection for weddings. Thus we stress the classy yet fun aspect of this project. Also, it would be preferable to use legible and interesting, but clear fonts. Clean and less cluttered is also a plus, but by all means just do what you think looks best.

Attached are the photos that we have available and fit our goals. There is no need to use them all, but if possible please stress the great range of options and the lovely clean wedding shots. Blue, White, Silver and a splash of pink have been used in the past for our logo, site, business cards, and older brochures so those are the preferred colors for this brochure. This brochure should trend feminine. Most of our clients are brides and mothers so that should be taken into consideration, but only to a point so that we don't close ourselves off to anyone.

I am attaching a logo, some photos strips, single shots, and instructions on the actual wording. Please let me know if you need anything else. Thank you in advance.
Updates

Target Market(s)

most of our clients are female, but the brochure shouldn't be so feminine as to dissuade males from becoming clients

Industry/Entity Type

School

Colors
f9d9e8
ffffff
f0f0f0
86cae7

Requirements
Nice to have
• A way of fitting in a variety of colorful photos to highlight our range, but while still maintaining a clean and ordered look.

```html
<!DOCTYPE html>
<html lang="en">
<head>
<meta charset="utf-8">
<title>Photo Booth Rentals – Inside Spread</title>
<link href="https://fonts.googleapis.com/css2?family=Montserrat:wght@400;600;700&family=Allura&display=swap" rel="stylesheet">
<style>
  :root{
    --page:#ffffff;
    --panel-blue:#cfe7ed;
    --panel-grey:#ececec;
    --pink:#f29bbc;
    --pink-deep:#ee86ae;
    --banner:#f4f6f7;
    --blue:#1a8ccf;
    --script-blue:#3a9fd6;
    --text:#4a4a4a;
    --title:#555555;
    --white:#ffffff;
  }
  *{margin:0;padding:0;box-sizing:border-box}
  html,body{width:1200px;height:1000px;overflow:hidden;background:var(--page)}
  body{position:relative;font-family:'Montserrat',sans-serif;color:var(--text)}
  .abs{position:absolute}
  .panel-main{left:103px;top:117px;width:662px;height:766px;background:var(--panel-blue)}
  .panel-side{left:765px;top:117px;width:330px;height:766px;background:var(--panel-grey)}
  .ribbon-band{left:103px;top:185px;width:992px;height:14px;background:var(--pink)}
  .ribbon-band.lower{top:589px;width:662px}
  .title-banner{width:220px;height:52px;background:var(--banner);border-radius:6px}
  .title-text{width:220px;text-align:center;font-family:'Allura',cursive;font-size:40px;line-height:52px;color:var(--title)}
  .bow{width:110px;height:50px;background:var(--pink-deep);border-radius:8px}
  .stats-box{left:458px;top:137px;width:283px;height:171px;background:var(--pink);border-radius:14px;color:var(--white);text-align:center;padding-top:8px;font-size:10.5px;line-height:14px}
  .stats-box strong{display:block;font-size:14px;line-height:16px;font-weight:700}
  .stats-box b{font-size:13.5px;font-weight:700}
  .section-heading{font-weight:700;color:var(--blue);font-size:18.5px;line-height:23px;text-align:center;letter-spacing:.2px}
  .booth-name{font-family:'Allura',cursive;font-weight:400;color:var(--script-blue);font-size:24px;line-height:22px}
  .body-copy{font-size:11.3px;line-height:13.3px;color:var(--text)}
  .photo{border:2px solid var(--white)}
  .upgrade-heading{left:250px;top:584px;width:367px;background:var(--panel-blue)}
  .upgrade-sub{left:250px;top:612px;width:367px;text-align:center;font-size:10.5px;font-weight:700;color:var(--blue)}
  .upgrade-item h3{font-size:13.8px;font-weight:700;color:var(--blue);text-decoration:underline;line-height:18px;margin-bottom:1px}
  .upgrade-item p{font-size:11.3px;line-height:15.3px}
</style>
</head>
<body>
  <div class="abs panel-main"></div>
  <div class="abs panel-side"></div>
  <div class="abs ribbon-band"></div>

  <div class="abs bow" role="img" aria-label="Pink satin bow with trailing ribbons" style="left:232px;top:175px"></div>
  <div class="abs title-banner" role="img" aria-label="Scroll banner ornament" style="left:158px;top:136px"></div>
  <h2 class="abs title-text" style="left:158px;top:136px">About Us</h2>

  <div class="abs bow" role="img" aria-label="Pink satin bow with trailing ribbons" style="left:878px;top:175px"></div>
  <div class="abs title-banner" role="img" aria-label="Scroll banner ornament" style="left:818px;top:136px"></div>
  <h2 class="abs title-text" style="left:818px;top:136px">Upgrades</h2>

  <div class="abs stats-box">
    <strong>"BEST OF WEDDINGS" WINNER.</strong>
    <strong>FIVE-STAR RATED</strong>
    on VOWLIST.COM, AISLEVIEW.COM, and LOCALSTAR.<br>
    Nearly 2,000 happy clients in
    <strong>6+YEARS OF SERVICE.</strong>
    <strong>HIGHEST QUALITY</strong>
    photo booth photos available.<br>
    <b>EXPERIENCED STAFF</b> of friends and<br>family that care deeply for our business &amp;<br>your happiness.
  </div>

  <h1 class="abs section-heading" style="left:115px;top:263px;width:308px">CHOOSE YOUR STYLE OF PHOTO&nbsp; BOOTH EXPERIENCE</h1>

  <h2 class="abs booth-name" style="left:124px;top:319px">Our Classic Booth</h2>
  <p class="abs body-copy" style="left:124px;top:343px;width:296px">At 7'x5' our classic booth stands elegant and<br>spacious. The largest fully enclosed booth on the<br>market, the Classic Booth is designed to look classy<br>in any venue, with a lovely black exterior and your<br>choice of accent curtain to match your event colors<br>and theme.</p>

  <h2 class="abs booth-name" style="left:458px;top:320px">The Open Booth</h2>
  <p class="abs body-copy" style="left:458px;top:344px;width:290px">The Open Booth consists of a stylish photo booth<br>kiosk and a backdrop of your choosing. People<br>seem to&nbsp; gravitate toward the Open Booth to enjoy<br>the spectacle and inevitably take part in the fun<br>themselves.</p>

  <div class="abs photo" role="img" aria-label="Classic enclosed booth with red curtain and red carpet" style="left:104px;top:431px;width:164px;height:142px;background:linear-gradient(135deg,#1c1530,#3d2a5a 55%,#b0233f)"></div>
  <div class="abs photo" role="img" aria-label="Guests posing in front of a blue backdrop" style="left:269px;top:431px;width:166px;height:142px;background:linear-gradient(135deg,#8cc3e0,#d9ecf5 55%,#c49a86)"></div>
  <div class="abs photo" role="img" aria-label="Open booth kiosk set up by a city-view window" style="left:435px;top:431px;width:164px;height:142px;background:linear-gradient(135deg,#e9eef2,#7fa2bd 50%,#3b4a5c)"></div>
  <div class="abs photo" role="img" aria-label="Guest with props in front of a sponsor backdrop" style="left:599px;top:431px;width:166px;height:142px;background:linear-gradient(135deg,#f2f2f2,#d9d9d9 50%,#d8625e)"></div>

  <div class="abs ribbon-band lower"></div>
  <h2 class="abs section-heading upgrade-heading">UPGRADE TO A SPECIALTY BOOTH</h2>
  <p class="abs upgrade-sub">- COMPLETELY UNIQUE ONE OF A KIND DESIGNS</p>

  <h3 class="abs booth-name" style="left:124px;top:634px">The Party Booth</h3>
  <p class="abs body-copy" style="left:124px;top:657px;width:300px">Our Party Booth is a Pink &amp; Black Damask version of<br>our Classic Booth with a Pink LED lit Photo Booth<br>Kiosk within.</p>

  <h3 class="abs booth-name" style="left:124px;top:707px">The Shore Booth</h3>
  <p class="abs body-copy" style="left:124px;top:730px;width:300px">This shimmery Blue version of our Classic Booth<br>comes with ocean themed props, Blue Led lit Photo<br>Kiosk, wooden dock post &amp; rope stanchions and<br>blue carpet.</p>

  <h3 class="abs booth-name" style="left:124px;top:794px">The SpiceBooth</h3>
  <p class="abs body-copy" style="left:124px;top:817px;width:300px">This option is a lovely Red and Purple, accented with<br>gold, with a purple LED lit kiosk inside, perfect for<br>a Southeast Asian affair.</p>

  <div class="abs photo" role="img" aria-label="Pink and black damask party booth" style="left:458px;top:634px;width:141px;height:99px;background:linear-gradient(135deg,#5a4a3c,#a1386e 55%,#e7d9c6)"></div>
  <div class="abs photo" role="img" aria-label="Shimmery blue shore booth" style="left:599px;top:634px;width:142px;height:99px;background:linear-gradient(135deg,#4a3d33,#2d6f99 55%,#d8c8b4)"></div>
  <div class="abs photo" role="img" aria-label="Guest posing inside the red and gold SpiceBooth" style="left:458px;top:733px;width:283px;height:138px;background:linear-gradient(135deg,#c9234a,#7a1430 55%,#d2a15a)"></div>

  <div class="abs upgrade-item" style="left:780px;top:257px;width:295px">
    <h3>THE JAZZBOOTH</h3>
    <p>This is a Roaring Twenties themed upgrade- 1920's<br>style props, gold or silver sequin backdrop for your<br>photos, Jazz Age themed kiosk screen. We also<br>adorn your classic booth rental with a gold curtain,<br>giving you that black and<br>gold combo that screams<br>"Jazz Age".</p>
  </div>
  <div class="abs upgrade-item" style="left:780px;top:397px;width:165px">
    <h3>THE HOLLYWOOD</h3>
    <p>This is an upgrade that<br>adds a red carpet, brass<br>stancions, and red velvet<br>rope to your package,<br>plus a Hollywood Prop<br>upgrade.</p>
  </div>
  <div class="abs upgrade-item" style="left:780px;top:522px;width:165px">
    <h3>SPECIALTY BOOTH</h3>
    <p>Upgrade to The Party<br>Booth, The Shore Booth,<br>or The SpiceBooth.</p>
  </div>
  <div class="abs upgrade-item" style="left:780px;top:601px;width:170px">
    <h3>SOCIAL MEDIA KIOSK</h3>
    <p>Enable your guests to<br>upload their photos<br>straight to Friendbook,<br>Chirper, and their email.<br>Great for corporate clients<br>looking to increase their<br>brand exposure.</p>
  </div>
  <div class="abs upgrade-item" style="left:780px;top:739px;width:300px">
    <h3>GREEN SCREEN</h3>
    <p style="margin-top:8px">Insert any backdrop youcan think of!</p>
  </div>
  <div class="abs upgrade-item" style="left:780px;top:796px;width:300px">
    <h3>CUSTOM STEP &amp; REPEAT BACKDROP</h3>
    <p>A branded or personalized banner is a great way to<br>commemorate an occasion or promote your brand.</p>
  </div>

  <div class="abs photo" role="img" aria-label="Twenties themed props with feathers and masks" style="left:953px;top:380px;width:128px;height:108px;background:linear-gradient(135deg,#0d0d10,#2a3440 55%,#6b6f75)"></div>
  <div class="abs photo" role="img" aria-label="Couple posing with costume props on a green screen" style="left:953px;top:489px;width:128px;height:108px;background:linear-gradient(135deg,#2f8a5a,#3fa36d 55%,#1f5e3c)"></div>
  <div class="abs photo" role="img" aria-label="Social media kiosk on a patterned rug" style="left:953px;top:598px;width:128px;height:108px;background:linear-gradient(135deg,#1f2a1e,#3c4f3a 50%,#2a3d6a)"></div>
</body>
</html>
```